Business card design for new eCommerce site focusing on integrity and strong businsess tactics

We need a business card that will stand out and be memorable. Something with color that matches our company logo colors. Think high end version of Pactivo. There are 2 logos provided. The parent company is called Amber Ledge Partners and we are presenting a new and very exciting eCommerce site called BrightHarborTrade.example.

Target Market(s)

Our target markets are in the Activities, Food and Beverage, Health and Beauty

Industry/Entity Type

Marketing

Contact Information for Business Card

We have 4 members that need cards...I will provide all info to the winner of the design contest
Business Address is
4870 West 63rd Avenue, Suite C207
Phoenix AZ 85731

Font styles to use
Serif
Sans Serif

Colors

Designer to choose colors to be used in the design.

Requirements
Must have
• The card must be memorable...should be unique in design but must exude integrity and be playful .
• I have provided several colors or our parent company...please feel free to use which ever
Nice to have
• I will leave this up to you. Feel free to use other images of your choosing that wraps around our client.....Activities, Dining, Health, Beauty
Should not have
• just dont be boring

```html
<!DOCTYPE html>
<html lang="en">
<head>
<meta charset="utf-8">
<title>Amber Ledge Partners – Business Card</title>
<link rel="stylesheet" href="https://fonts.googleapis.com/css2?family=Open+Sans:wght@400;600;700&display=swap">
<style>
  :root {
    --brand-blue: #2b7bb1;
    --brand-blue-soft: #4a91c1;
    --brand-green: #9cc73b;
    --ink-grey: #555b60;
    --card-white: #ffffff;
    --backdrop: #e6e7e8;
  }
  * { margin: 0; padding: 0; box-sizing: border-box; }
  html, body { width: 1200px; height: 1000px; overflow: hidden; }
  body {
    background: var(--backdrop);
    font-family: "Open Sans", Arial, sans-serif;
    position: relative;
  }
  .card {
    position: absolute;
    left: 255px;
    width: 665px;
    height: 378px;
    border-radius: 18px;
    overflow: hidden;
    box-shadow: 0 4px 10px rgba(0,0,0,0.18);
  }
  .card--front { top: 102px; background: var(--card-white); }
  .card--back { top: 520px; background: var(--brand-blue); color: var(--card-white); }

  .holder-name {
    position: absolute; left: 30px; top: 76px;
    color: var(--brand-blue); font-weight: 700; font-size: 21px;
  }
  .holder-role {
    position: absolute; left: 30px; top: 102px;
    color: var(--ink-grey); font-size: 16px;
  }
  .contact-list {
    position: absolute; left: 30px; top: 174px;
    list-style: none; color: var(--ink-grey); font-size: 14px; letter-spacing: 0.3px;
  }
  .contact-list li { display: flex; align-items: center; height: 21px; }
  .contact-list svg { width: 12px; height: 12px; margin-right: 13px; fill: var(--brand-blue); }
  .address {
    position: absolute; left: 33px; top: 274px;
    color: var(--ink-grey); font-size: 14px; line-height: 21px; letter-spacing: 0.3px;
  }
  .company-mark__dot {
    position: absolute; left: 450px; top: 70px;
    width: 90px; height: 90px; border-radius: 50%;
    border: 6px solid var(--brand-green);
  }
  .company-mark__name {
    position: absolute; right: 30px; top: 244px;
    color: var(--brand-green); font-weight: 600; font-size: 36px;
    line-height: 44px; white-space: nowrap;
  }
  .front-band { position: absolute; left: 0; bottom: 0; width: 665px; height: 40px; }

  .brand-area {
    position: absolute; left: 20px; top: 10px;
    width: 300px; height: 360px; border-radius: 14px;
    background: linear-gradient(160deg, var(--brand-blue-soft), var(--brand-blue));
  }
  .site-block {
    position: absolute; right: 38px; bottom: 30px; text-align: right;
  }
  .site-block__dot {
    display: inline-block; width: 14px; height: 14px; border-radius: 50%;
    background: var(--card-white); margin-right: 8px; vertical-align: middle;
  }
  .site-block__name { font-size: 25px; font-weight: 600; vertical-align: middle; }
  .site-block__tagline { font-size: 13px; letter-spacing: 1.2px; margin-top: 2px; }
  .site-block__web { font-size: 14px; letter-spacing: 0.6px; margin-top: 3px; }
</style>
</head>
<body>
  <section class="card card--front">
    <h1 class="holder-name">Daniel Reyes</h1>
    <p class="holder-role">Founder</p>
    <ul class="contact-list">
      <li><svg viewBox="0 0 12 12"><path d="M3 0h6v12H3z M4 1v9h4V1z" fill-rule="evenodd"/></svg>0427 555 019</li>
      <li><svg viewBox="0 0 12 12"><path d="M0 2h12v8H0z M0 2l6 4 6-4" /></svg>info@brightharbortrade.example</li>
      <li><svg viewBox="0 0 12 12"><path d="M5 1a4 4 0 1 1 0 8a4 4 0 0 1 0-8zm0 1.6a2.4 2.4 0 1 0 0 4.8a2.4 2.4 0 0 0 0-4.8zM7.6 8.4l1.2-1.2L12 10.4 10.8 11.6z"/></svg>www.brightharbortrade.example</li>
    </ul>
    <p class="address">4870 West 63rd Avenue,<br>Suite C207 Phoenix AZ 85731</p>
    <span class="company-mark__dot"></span>
    <p class="company-mark__name">Amber Ledge Partners</p>
    <svg class="front-band" viewBox="0 0 665 40" preserveAspectRatio="none">
      <rect x="0" y="18" width="390" height="5" fill="var(--brand-green)"/>
      <path d="M0 23 H380 C400 23 395 10 430 10 H665 V40 H0 Z" fill="var(--brand-blue)"/>
      <path d="M380 18 C395 18 400 10 420 10 L430 10 C400 10 400 23 380 23 Z" fill="var(--brand-green)"/>
    </svg>
  </section>

  <section class="card card--back">
    <div class="brand-area" role="img" aria-label="Large brand mark of BrightHarborTrade.example"></div>
    <div class="site-block">
      <p><span class="site-block__dot"></span><span class="site-block__name">BrightHarborTrade.example</span></p>
      <p class="site-block__tagline">Activities-Dining-Health-Beauty</p>
      <p class="site-block__web">www.amberledgepartners.example</p>
    </div>
  </section>
</body>
</html>
```